Marlowe Group needs a business card

I would like the card to be simple but modern and elegant.
I like black and white.
or black and gold.
we are a private finance lender and also are involved in property and property developments.

please look at the business card photos i provided i would like M.G only one one side and all the other details on the other side use fonts that tie in with my theme.

Industry/Entity Type

Finance

Contact Information for Business Card

Marlowe Group (M.G) Daniel Marlowe M: 0413586207 E: danmarl@inboxmail.test

Font styles to use
Other font styles liked:
• Use fonts that would reflect our business

Colors
000000
ffffff

Requirements
Must have
• one side of details
• other side has either M.G or Marlowe Group like in the photos provided

```html
<!DOCTYPE html>
<html lang="en">
<head>
<meta charset="UTF-8">
<title>Marlowe Group — Business Card</title>
<link rel="stylesheet" href="https://fonts.googleapis.com/css2?family=Cinzel:wght@400&family=Open+Sans:wght@400;700&display=swap">
<style>
  :root {
    --page-bg: #e6e4e2;
    --card-black: #000000;
    --gold: #f2c12e;
    --gold-deep: #e3b024;
    --white: #ffffff;
    --panel-dark: #2a2a2a;
    --panel-mid: #5a5755;
    --panel-light: #8a8582;
  }
  * { margin: 0; padding: 0; box-sizing: border-box; }
  html, body {
    width: 1200px;
    height: 900px;
    overflow: hidden;
    background: var(--page-bg);
  }
  .card {
    position: absolute;
    left: 148px;
    top: 170px;
    width: 904px;
    height: 559px;
    background: var(--card-black);
    box-shadow: 0 12px 30px rgba(0, 0, 0, 0.25);
  }
  .company-name {
    position: absolute;
    left: 46px;
    top: 116px;
    font-family: "Cinzel", serif;
    font-size: 33px;
    line-height: 44px;
    font-weight: 400;
    letter-spacing: 0.5px;
    color: var(--gold-deep);
    white-space: nowrap;
  }
  .person-name {
    position: absolute;
    left: 43px;
    top: 250px;
    font-family: "Open Sans", sans-serif;
    font-size: 32px;
    line-height: 44px;
    font-weight: 700;
    color: var(--gold);
    white-space: nowrap;
  }
  .contact-list {
    position: absolute;
    left: 46px;
    top: 340px;
    list-style: none;
    font-family: "Open Sans", sans-serif;
    font-size: 23px;
    color: var(--white);
  }
  .contact-item {
    display: flex;
    align-items: center;
    height: 38px;
    white-space: nowrap;
  }
  .contact-icon {
    width: 18px;
    height: 18px;
    margin-right: 13px;
    flex: none;
  }
  .brand-panel {
    position: absolute;
    left: 437px;
    top: 97px;
    width: 421px;
    height: 365px;
    background: linear-gradient(100deg, var(--panel-light) 0%, var(--panel-mid) 35%, var(--panel-dark) 70%, var(--panel-mid) 100%);
    display: flex;
    align-items: center;
    justify-content: center;
  }
  .brand-mark {
    font-family: "Cinzel", serif;
    font-size: 110px;
    line-height: 1;
    font-weight: 400;
    color: var(--gold);
    letter-spacing: 4px;
    white-space: nowrap;
  }
</style>
</head>
<body>
  <section class="card">
    <p class="company-name">Marlowe Group</p>
    <p class="person-name">Daniel Marlowe</p>
    <ul class="contact-list">
      <li class="contact-item">
        <svg class="contact-icon" viewBox="0 0 24 24" aria-hidden="true">
          <path fill="var(--gold)" d="M6.6 10.8a15.2 15.2 0 0 0 6.6 6.6l2.2-2.2a1 1 0 0 1 1-.25 11.4 11.4 0 0 0 3.6.57 1 1 0 0 1 1 1V20a1 1 0 0 1-1 1A17 17 0 0 1 3 4a1 1 0 0 1 1-1h3.5a1 1 0 0 1 1 1c0 1.25.2 2.45.57 3.57a1 1 0 0 1-.25 1z"/>
        </svg>
        <span class="contact-text">0413586207</span>
      </li>
      <li class="contact-item">
        <svg class="contact-icon" viewBox="0 0 24 24" aria-hidden="true">
          <rect x="2" y="5" width="20" height="14" fill="var(--gold)"/>
          <path d="M2.5 5.5l9.5 7 9.5-7" fill="none" stroke="var(--card-black)" stroke-width="1.8"/>
        </svg>
        <span class="contact-text">danmarl@inboxmail.test</span>
      </li>
    </ul>
    <div class="brand-panel" role="img" aria-label="Softly blurred interior photograph behind the company initials">
      <span class="brand-mark">M.G</span>
    </div>
  </section>
</body>
</html>
```